An internal sign in a physiotherapy clinic with gym. About working hard

We are a physiotherapy clinic / gym and we are wanting an internal wall to be a large sign with a great slogan
We are after 3 parts to it
1. The image / backdrop
2. The slogan
3. Our clinic logo

I have attached some images of the concept of what we are after. It can be climbing a mountain, rockclimbing and even hard work in a gym.

The slogan is:
"IF IT DOESN'T CHALLENGE YOU, IT WON'T CHANGE YOU"

Logo
I have attached a few different versions of our logo to assist you in the sign based on the background

THE SIGN SIZE WILL BE:
2935mm wide x 1885mm high

```html
<!DOCTYPE html>
<html lang="en">
<head>
<meta charset="utf-8">
<title>If It Doesn't Challenge You – Wall Sign</title>
<link rel="stylesheet" href="https://fonts.googleapis.com/css2?family=Exo+2:ital,wght@0,800;1,800;1,900&display=swap">
<style>
  :root {
    --page: #e4e4e4;
    --sign-bg: #08090b;
    --photo-dark: #141518;
    --photo-wall: #4a4a4c;
    --photo-concrete: #6d6d6f;
    --photo-skin: #b98466;
    --photo-skin-deep: #7a5240;
    --photo-steel: #c9cacc;
    --photo-teal: #1fa9a6;
    --cyan: #35c6f0;
    --white: #ffffff;
  }
  * { margin: 0; padding: 0; box-sizing: border-box; }
  html, body {
    width: 805px;
    height: 1200px;
    overflow: hidden;
    background: var(--page);
  }
  .canvas {
    position: relative;
    width: 805px;
    height: 1200px;
    display: flex;
    align-items: center;
    justify-content: center;
  }
  .sign {
    position: relative;
    width: 805px;
    height: 517px;
    background: var(--sign-bg);
    overflow: hidden;
    font-family: "Exo 2", "Arial Black", sans-serif;
  }
  .sign__photo {
    position: absolute;
    top: 0;
    right: 0;
    width: 560px;
    height: 100%;
    background:
      radial-gradient(ellipse 16% 12% at 84% 30%, var(--photo-steel) 0%, rgba(201,202,204,0.5) 45%, rgba(0,0,0,0) 100%),
      radial-gradient(ellipse 14% 16% at 24% 44%, rgba(201,202,204,0.75) 0%, rgba(120,120,124,0.4) 50%, rgba(0,0,0,0) 100%),
      radial-gradient(ellipse 20% 18% at 50% 24%, var(--photo-skin) 0%, rgba(185,132,102,0.55) 50%, rgba(0,0,0,0) 100%),
      radial-gradient(ellipse 30% 26% at 52% 70%, var(--photo-skin) 0%, var(--photo-skin-deep) 45%, rgba(0,0,0,0) 100%),
      radial-gradient(ellipse 34% 10% at 82% 96%, rgba(31,169,166,0.7) 0%, rgba(0,0,0,0) 100%),
      linear-gradient(90deg, var(--photo-dark) 0%, var(--photo-wall) 45%, var(--photo-concrete) 78%, var(--photo-wall) 100%);
  }
  .sign__photo::after {
    content: "";
    position: absolute;
    inset: 0;
    background: linear-gradient(90deg, var(--sign-bg) 0%, rgba(8,9,11,0) 30%);
  }
  .slogan {
    position: absolute;
    left: 48px;
    top: 26px;
    font-style: italic;
    font-weight: 900;
    text-transform: uppercase;
    line-height: 0.9;
    letter-spacing: 1px;
    color: var(--white);
  }
  .slogan__line { display: block; }
  .slogan__line--small { font-size: 44px; }
  .slogan__line--large { font-size: 104px; color: var(--cyan); margin: 2px 0 0; }
  .slogan__line--you { font-size: 72px; color: var(--cyan); }
  .slogan__accent { color: var(--cyan); }
  .brand {
    position: absolute;
    left: 60px;
    top: 402px;
    display: flex;
    align-items: center;
    gap: 10px;
    color: var(--white);
    font-weight: 800;
    font-style: normal;
    font-size: 19px;
    letter-spacing: 1px;
    line-height: 1.05;
    text-transform: uppercase;
  }
  .brand__mark {
    width: 16px;
    height: 16px;
    border-radius: 50%;
    background: var(--cyan);
    flex: none;
  }
</style>
</head>
<body>
  <main class="canvas">
    <section class="sign">
      <div class="sign__photo" role="img" aria-label="Photo of an athlete performing a heavy barbell squat in a dark concrete gym"></div>
      <h1 class="slogan">
        <span class="slogan__line slogan__line--small">If it doesn't</span>
        <span class="slogan__line slogan__line--large">Challenge</span>
        <span class="slogan__line slogan__line--small">It won't <span class="slogan__accent">change</span></span>
        <span class="slogan__line slogan__line--you">You</span>
      </h1>
      <div class="brand">
        <span class="brand__mark"></span>
        <span class="brand__name">Hartwell<br>Sports Medicine</span>
      </div>
    </section>
  </main>
</body>
</html>
```